KR Appraisals website redesign

I would like to refresh my existing website of www.krappraisals-example.com with new graphics, look and feel, as well as updated structure and wording. Content and layout changes have been uploaded to this project Brief.

My existing website has a dark feel. I am now looking for a light and energetic feel. Financial Services is my industry, so the website should be reflect that. I would also like to reflect the concepts of Trust, Service and Expertise.

The website must be serious and upmarket.

Target Market(s)

Corporate board members, CFO's, treasurers and controllers
Auditors, tax advisors, private equity and venture capital asset managers, investors, tax authorities

Industry/Entity Type

Financial Service

Coding

Coded - Design and coding required

Number of Pages Required

5+ page

Font styles to use
Sans Serif
Other font styles liked:
• Designer can choose another modern font

Colors
0355a3
3277b5
85acd3
eaf1f7
f37122
f68d4d
9bcb3c
acd037
cadf82

Requirements
Must have
• Good hi resolution pictures that convey "Finance", "Trust", "Service" or "Expertise".
• An anti-bot (such as Captcha) mechanism in the contact form.
Should not have
• Must not have all content on one rolling screen.

```html
<!DOCTYPE html>
<html lang="en">
<head>
<meta charset="utf-8">
<title>KR Appraisals</title>
<link href="https://fonts.googleapis.com/css2?family=Lato:wght@300;400;700;900&display=swap" rel="stylesheet">
<style>
:root{
  --ink:#2b2f38;
  --blue:#0355a3;
  --blue-deep:#034585;
  --blue-mid:#3277b5;
  --blue-soft:#85acd3;
  --blue-pale:#eaf1f7;
  --orange:#f37122;
  --orange-soft:#f68d4d;
  --green:#9bcb3c;
  --green-soft:#cadf82;
  --white:#ffffff;
}
*{margin:0;padding:0;box-sizing:border-box}
html,body{width:1200px;height:3769px;overflow:hidden}
body{font-family:'Lato',sans-serif;color:var(--ink);background:var(--blue-deep);position:relative}
.abs{position:absolute}
section,header,footer{position:absolute;left:0;width:1200px}

/* top bar */
.topbar{top:0;height:32px;background:var(--blue-pale)}
.topbar .welcome{left:136px;top:10px;font-size:10px;color:#7d8a99}
.topbar .lang{left:790px;top:10px;font-size:10px;color:#7d8a99}
.topbar .social{top:12px;width:8px;height:8px;border-radius:50%;background:var(--blue-mid)}
.btn-quote{background:var(--orange);color:#fff;font-size:11px;font-weight:700;text-transform:uppercase;display:flex;align-items:center;justify-content:center;letter-spacing:.3px}
.topbar .btn-quote{left:938px;top:0;width:120px;height:32px}

/* header */
.header{top:32px;height:96px;background:#fff}
.brand{left:136px;display:flex;align-items:center;gap:8px}
.brand .mark{width:12px;height:12px;background:var(--blue)}
.brand .name{font-size:19px;font-weight:400;color:var(--blue);letter-spacing:.5px}
.nav{top:52px;font-size:11px;font-weight:700;color:#222;text-transform:uppercase}
.search{left:1034px;top:48px}

/* hero */
.hero{top:128px;height:519px;background:linear-gradient(180deg,#f6f9fc 0%,#dfeaf5 45%,#bcd2e8 100%)}
.hero-photo{left:0;top:0;width:1200px;height:519px;background:linear-gradient(115deg,rgba(255,255,255,.6) 0%,rgba(133,172,211,.25) 50%,rgba(50,119,181,.25) 100%)}
.hero h1{left:132px;top:112px;font-size:44px;font-weight:900;color:var(--blue-deep);letter-spacing:-.5px;white-space:nowrap}
.hero .big{left:128px;top:158px;font-size:100px;font-weight:900;color:var(--blue-soft);letter-spacing:-2px;line-height:1}
.btn{font-size:11px;text-transform:uppercase;display:flex;align-items:center;justify-content:center;height:40px}
.btn-light{left:136px;top:369px;width:136px;background:#fff;color:var(--blue)}
.btn-dark{left:279px;top:369px;width:135px;background:var(--blue);color:#fff}

/* cta */
.cta{top:647px;height:102px;background:var(--blue)}
.cta h2{left:136px;top:28px;font-size:25px;font-weight:700;color:#fff}
.cta p{left:138px;top:62px;font-size:15px;font-weight:300;color:var(--blue-pale)}
.cta .btn-quote{left:922px;top:36px;width:136px;height:38px}

/* headings */
.sec-title{left:0;width:1200px;text-align:center;font-size:32px;font-weight:300;color:#33404f;letter-spacing:.5px}
.sec-rule{left:570px;width:60px;height:2px;background:var(--orange)}

/* about */
.about{top:749px;height:658px;background:#fff}
.about .sec-title{top:72px}
.about .sec-rule{top:135px}
.about .copy{left:200px;width:800px;text-align:center;font-size:9.5px;line-height:18px;color:#555}
.cards{left:138px;top:366px;width:920px;height:224px;display:flex;box-shadow:0 2px 10px rgba(0,0,0,.12)}
.card{flex:1;background:#fff;text-align:center;padding-top:30px;position:relative}
.card h3{font-size:17px;font-weight:700;color:#222;margin-top:14px}
.card p{font-size:9.5px;line-height:18px;color:#666;width:220px;margin:8px auto 0}
.card.is-active{background:linear-gradient(135deg,#3277b5 0%,#0355a3 60%,#034585 100%)}
.card.is-active h3{color:#fff}
.card.is-active p{color:var(--blue-pale)}

/* stats */
.stats{top:1407px;height:407px;background:linear-gradient(100deg,#3277b5 0%,#0355a3 50%,#034585 100%)}
.stats-photo{left:60px;top:60px;width:400px;height:330px;background:radial-gradient(ellipse at 50% 55%,rgba(155,203,60,.3) 0%,rgba(133,172,211,.15) 50%,rgba(0,0,0,0) 75%)}
.stats h2{left:0;width:1200px;text-align:center;top:66px;font-size:24px;font-weight:300;color:#fff}
.stat{width:200px;text-align:center;color:#fff}
.stat .num{font-size:40px;font-weight:900;line-height:1;margin-top:4px}
.stat .lbl{font-size:11px;font-weight:700;margin-top:12px}
.contact-frame{left:809px;top:192px;width:282px;height:274px;border:1px solid rgba(133,172,211,.7)}
.contact-box{left:793px;top:232px;width:269px;height:201px;background:var(--orange);text-align:center;color:#fff;z-index:2}
.contact-box .k{font-size:12px;font-weight:900;letter-spacing:1.5px;margin-top:40px}
.contact-box .phone{font-size:24px;font-weight:300;margin-top:18px}
.contact-box .or{font-size:9px;margin-top:6px;color:#ffe1cd}
.contact-box .mail{font-size:15.5px;font-weight:300;margin-top:10px}

/* services */
.services{top:1814px;height:427px;background:#fff}
.services .sec-title{top:72px}
.services .sec-rule{top:135px}
.svc .ic{width:46px;height:46px;border-radius:50%;background:var(--orange);display:flex;align-items:center;justify-content:center}
.svc h3{position:absolute;left:62px;top:-8px;font-size:15px;font-weight:700;color:#222;white-space:nowrap}
.svc p{position:absolute;left:62px;top:16px;width:215px;font-size:7.5px;line-height:11px;color:#888}

/* team */
.team{top:2241px;height:571px;background:linear-gradient(180deg,#f6f9fc 0%,#eaf1f7 50%,#f6f9fc 100%)}
.team-photo{left:0;top:0;width:1200px;height:571px;background:radial-gradient(ellipse at 95% 10%,rgba(202,223,130,.35) 0%,rgba(255,255,255,0) 30%),radial-gradient(ellipse at 5% 70%,rgba(133,172,211,.35) 0%,rgba(255,255,255,0) 30%)}
.team .sec-title{top:74px}
.team .sec-rule{top:135px}
.member{top:179px;width:236px;height:319px;box-shadow:0 2px 8px rgba(0,0,0,.15)}
.member .portrait{width:236px;height:243px;background:linear-gradient(180deg,#dfe3e8 0%,#a3a9b1 60%,#454b55 100%)}
.member .portrait.color{background:linear-gradient(180deg,#d3dce6 0%,#c9a58f 55%,#2f3a4a 100%)}
.member .plate{height:76px;background:var(--blue);text-align:center;color:#fff;padding-top:14px}
.member .plate.accent{background:var(--orange)}
.member .plate b{font-size:14px;font-weight:700}
.member .plate small{display:block;font-size:8px;letter-spacing:1.2px;line-height:11px;margin-top:8px;color:var(--blue-pale)}
.member .dots{display:flex;gap:28px;justify-content:center;margin-top:10px}
.member .dots span{width:15px;height:15px;border:1px solid #fff;border-radius:50%}

/* callback */
.callback{top:2812px;height:285px;background:linear-gradient(100deg,#3277b5 0%,#0355a3 55%,#034585 100%)}
.callback-photo{left:640px;top:0;width:560px;height:285px;background:radial-gradient(ellipse at 60% 40%,rgba(133,172,211,.4) 0%,rgba(0,0,0,0) 65%)}
.callback h2{left:0;width:1200px;text-align:center;top:66px;font-size:32px;font-weight:300;color:#fff}
.callback p{left:320px;width:560px;text-align:center;top:124px;font-size:13px;line-height:18px;color:var(--blue-pale)}
.field{top:181px;width:224px;height:40px;border:1px solid rgba(255,255,255,.5);color:#d5e3f0;font-size:12.5px;padding:12px 10px}
.submit{left:831px;top:181px;width:224px;height:40px;background:var(--orange);color:#fff;font-size:13px;font-weight:700;display:flex;align-items:center;justify-content:center;gap:8px}

/* partners */
.partners{top:3097px;height:104px;background:#fff}
.partner{top:36px;height:32px;background:#2a2f38;border-radius:3px}

/* footer */
.footer{top:3201px;height:401px;background:var(--blue)}
.footer-frame{left:133px;top:39px;width:457px;height:321px;border:1px solid rgba(255,255,255,.4);border-right:none}
.footer .brand-f{left:198px;top:110px;display:flex;align-items:center;gap:8px}
.footer .brand-f .mark{width:12px;height:12px;background:var(--blue-pale)}
.footer .brand-f .name{font-size:19px;color:var(--blue-pale);letter-spacing:.5px}
.city{font-size:23px;font-weight:300;color:var(--blue-pale)}
.addr{font-size:13px;line-height:17px;color:#fff}
.tel{font-size:13px;color:#fff;display:flex;align-items:center;gap:8px}
.map{left:590px;top:0;width:610px;height:401px;background:linear-gradient(135deg,#e4ecef 0%,#eef2f3 40%,#cfdfec 100%)}
.map-pin{left:1012px;top:36px;width:14px;height:14px;border-radius:50% 50% 50% 0;transform:rotate(-45deg);background:var(--orange)}
.to-top{left:1152px;top:358px;width:28px;height:28px;border-radius:50%;background:var(--orange);display:flex;align-items:center;justify-content:center}

.bottombar{top:3602px;height:167px;background:var(--blue-deep)}
.bottombar .copy{left:133px;top:15px;font-size:9px;color:var(--blue-soft)}
.bottombar .links{left:824px;top:15px;font-size:9px;color:var(--blue-soft)}
.bottombar .social{top:18px;width:7px;height:7px;border-radius:50%;background:var(--blue-soft)}
</style>
</head>
<body>

<header class="topbar">
  <div class="abs welcome">Welcome to KR Appraisals</div>
  <div class="abs lang">English &#8964;</div>
  <span class="abs social" style="left:855px"></span>
  <span class="abs social" style="left:879px"></span>
  <span class="abs social" style="left:903px"></span>
  <div class="abs btn-quote">Get a quote</div>
</header>

<header class="header">
  <div class="abs brand" style="top:50px"><span class="mark"></span><span class="name">KR APPRAISALS</span></div>
  <div class="abs nav" style="left:518px">Home</div>
  <div class="abs nav" style="left:594px">About us</div>
  <div class="abs nav" style="left:696px">Services</div>
  <div class="abs nav" style="left:790px">News</div>
  <div class="abs nav" style="left:865px">Career</div>
  <div class="abs nav" style="left:950px">Contacts</div>
  <svg class="abs search" width="18" height="18" viewBox="0 0 18 18"><circle cx="7" cy="7" r="5.5" fill="none" stroke="#444" stroke-width="2"/><line x1="11" y1="11" x2="16.5" y2="16.5" stroke="#444" stroke-width="2.5"/></svg>
</header>

<section class="hero">
  <div class="abs hero-photo" role="img" aria-label="Upward view of glass office towers in soft blue light"></div>
  <h1 class="abs">BUSINESS &amp; INTELECTUAL PROPERTY</h1>
  <div class="abs big">VALUATIONS</div>
  <div class="abs btn btn-light">About us</div>
  <div class="abs btn btn-dark">Our services</div>
</section>

<section class="cta">
  <h2 class="abs">Would you like to speak to one of our experts?</h2>
  <p class="abs">Just submityour contact details and we'll be in touch shortly</p>
  <div class="abs btn-quote">Get a quote</div>
</section>

<section class="about">
  <h2 class="abs sec-title">ABOUT US</h2>
  <div class="abs sec-rule"></div>
  <p class="abs copy" style="top:176px">KR Appraisals, founded in 2012, is a boutique valuation advisory practice servicing companies throughout Europe and North America. We have offices in Leiden and Amsterdam.<br>Through our affiliate partners, we also have offices in New York and London offering transfer pricing, derivatives modelling, and machinery &amp; equipment valuation.<br>Our clients come from a broad range of industries with valuations ranging between micro-cap and large-cap.</p>
  <p class="abs copy" style="top:248px">KR Appraisals assists companies with valuations of businesses, financial instruments, derivatives, personal property and intellectual property<br>(such as brand assets and patents) for transaction, fiscal, legal and accounting purposes, particularly in cross-border situations.<br>Through our bespoke approach and global network, we customize teams to the needs of our clients.<br>We also offer finance training to the international finance and banking sector through our Lowlands Finance Institute brand.</p>
  <div class="abs cards">
    <div class="card">
      <svg width="56" height="56" viewBox="0 0 56 56" fill="none" stroke="#0355a3" stroke-width="1.6"><circle cx="26" cy="30" r="20"/><circle cx="26" cy="30" r="13"/><circle cx="26" cy="30" r="6"/><line x1="26" y1="30" x2="48" y2="8"/><path d="M42 8h6v6"/></svg>
      <h3>Trust</h3>
      <p>Trust is paramount. Clients rely on KR Appraisals Services for confidentiality, transparency and independence.</p>
    </div>
    <div class="card is-active" role="img" aria-label="Two people shaking hands in a bright office">
      <svg width="56" height="56" viewBox="0 0 56 56" fill="none" stroke="#fff" stroke-width="1.6"><rect x="6" y="6" width="18" height="16" rx="2"/><rect x="30" y="6" width="18" height="16" rx="2"/><rect x="6" y="28" width="18" height="18" rx="2"/><rect x="30" y="28" width="18" height="18" rx="2"/><line x1="24" y1="14" x2="30" y2="14"/><line x1="15" y1="22" x2="15" y2="28"/><line x1="39" y1="22" x2="39" y2="28"/></svg>
      <h3>Service</h3>
      <p>Service is front and center in our product offerings. KR Appraisals Services considers the needs of all stakeholders and the personal needs of the client team involved.</p>
    </div>
    <div class="card">
      <svg width="56" height="56" viewBox="0 0 56 56" fill="none" stroke="#0355a3" stroke-width="1.6"><rect x="8" y="22" width="40" height="28"/><line x1="8" y1="36" x2="48" y2="36"/><line x1="28" y1="22" x2="28" y2="50"/><path d="M22 22V8h12v14"/><path d="M24 12h8"/></svg>
      <h3>Professionalism</h3>
      <p>The professionals behind KR Appraisals offer more than a decade of valuation expertise and maintain their commitment to continual professional development.</p>
    </div>
  </div>
</section>

<section class="stats">
  <div class="abs stats-photo" role="img" aria-label="Open hands beneath a glowing circuit board brain graphic"></div>
  <h2 class="abs">We advise you to make the right decision!</h2>
  <div class="abs stat" style="left:84px;top:144px">
    <svg width="36" height="36" viewBox="0 0 36 36" fill="none" stroke="#fff" stroke-width="1.4"><circle cx="18" cy="8" r="4"/><circle cx="10" cy="22" r="4"/><circle cx="26" cy="22" r="4"/><path d="M4 34c0-4 3-6 6-6s6 2 6 6M20 34c0-4 3-6 6-6s6 2 6 6"/></svg>
    <div class="num">120</div><div class="lbl">Companies consulted</div>
  </div>
  <div class="abs stat" style="left:324px;top:144px">
    <svg width="36" height="36" viewBox="0 0 36 36" fill="none" stroke="#fff" stroke-width="1.4"><line x1="18" y1="4" x2="18" y2="32"/><line x1="6" y1="10" x2="30" y2="10"/><path d="M6 10l-5 10h10z M30 10l-5 10h10z"/><line x1="11" y1="32" x2="25" y2="32"/></svg>
    <div class="num">10+</div><div class="lbl">Years of experience</div>
  </div>
  <div class="abs stat" style="left:563px;top:144px">
    <svg width="36" height="36" viewBox="0 0 36 36" fill="none" stroke="#fff" stroke-width="1.4"><circle cx="20" cy="9" r="5"/><path d="M3 24h8l6 3h8c2 0 2 3 0 3h-9M11 24l6-4h6"/><path d="M3 32l10 0 8 2 12-6"/></svg>
    <div class="num">200+</div><div class="lbl">Satisfied customers</div>
  </div>
  <div class="abs contact-frame"></div>
  <div class="abs contact-box">
    <div class="k">CONTACT US NOW!</div>
    <div class="phone">+31 70 555 0142</div>
    <div class="or">or</div>
    <div class="mail">info@krappraisals-example.com</div>
  </div>
</section>

<section class="services">
  <h2 class="abs sec-title">OUR SERVICES</h2>
  <div class="abs sec-rule"></div>

  <div class="abs svc" style="left:131px;top:204px">
    <div class="ic"><svg width="22" height="22" viewBox="0 0 22 22" fill="none" stroke="#fff" stroke-width="1.4"><circle cx="11" cy="11" r="9"/><path d="M2 11h18M11 2c3 3 3 15 0 18M11 2c-3 3-3 15 0 18"/></svg></div>
    <h3>Transaction Support</h3>
    <p>KR Appraisals Services helps you understand the value of an investment in your terms and that of your counterparty.</p>
  </div>
  <div class="abs svc" style="left:447px;top:204px">
    <div class="ic"><svg width="22" height="22" viewBox="0 0 22 22" fill="none" stroke="#fff" stroke-width="1.4"><rect x="2" y="4" width="18" height="12"/><path d="M5 13l4-4 3 3 5-5"/><line x1="7" y1="19" x2="15" y2="19"/></svg></div>
    <h3>Financial Reporting</h3>
    <p>Accounting procedures require post-transaction valuations concerning goodwill (PPA), acquired intangible assets and impairment testing.</p>
  </div>
  <div class="abs svc" style="left:761px;top:204px">
    <div class="ic"><svg width="22" height="22" viewBox="0 0 22 22" fill="none" stroke="#fff" stroke-width="1.4"><circle cx="11" cy="11" r="5"/><path d="M11 1v4M11 17v4M1 11h4M17 11h4M4 4l3 3M15 15l3 3M4 18l3-3M15 7l3-3"/></svg></div>
    <h3>Fiscal Valuations</h3>
    <p>KR Appraisals Services assesses the value of equity investments for Dutch fiscal purposes, reflecting both current market trends and valuation theory.</p>
  </div>
  <div class="abs svc" style="left:131px;top:320px">
    <div class="ic"><svg width="22" height="22" viewBox="0 0 22 22" fill="none" stroke="#fff" stroke-width="1.4"><line x1="11" y1="2" x2="11" y2="20"/><line x1="3" y1="6" x2="19" y2="6"/><path d="M3 6l-2 6h4z M19 6l-2 6h4z"/><line x1="6" y1="20" x2="16" y2="20"/></svg></div>
    <h3>Legal Support</h3>
    <p>Dutch law requires a contribution statement when a company is initially funded with equity that states, amongst other things, the value of the contributed shares and the valuation method applied.</p>
  </div>
  <div class="abs svc" style="left:447px;top:320px">
    <div class="ic"><svg width="22" height="22" viewBox="0 0 22 22" fill="none" stroke="#fff" stroke-width="1.4"><rect x="3" y="8" width="16" height="12"/><line x1="3" y1="14" x2="19" y2="14"/><line x1="11" y1="8" x2="11" y2="20"/><path d="M8 8V3h6v5"/></svg></div>
    <h3>Capital Advisory</h3>
    <p>Raising capital for your company is a long and arduous process. The stakes are high. KR Appraisals works with its global network of capital advisory experts to provide you with trusted, professional assistance.</p>
  </div>
  <div class="abs svc" style="left:761px;top:320px">
    <div class="ic"><svg width="22" height="22" viewBox="0 0 22 22" fill="none" stroke="#fff" stroke-width="1.4"><circle cx="11" cy="9" r="7"/><path d="M8 16v4h6v-4"/><path d="M8 9h6M11 6v6"/></svg></div>
    <h3>Finance Training</h3>
    <p>Open-enrollment training to the professional finance and banking markets is offered through our professional training division.</p>
  </div>
</section>

<section class="team">
  <div class="abs team-photo" role="img" aria-label="Soft blurred desk with papers and a coffee cup"></div>
  <h2 class="abs sec-title">MEET OUR TEAM</h2>
  <div class="abs sec-rule"></div>
  <div class="abs member" style="left:130px">
    <div class="portrait" role="img" aria-label="Black and white portrait of Martin Hale"></div>
    <div class="plate"><b>Martin Hale</b><small>KR Appraisals<br>Managing Director</small></div>
  </div>
  <div class="abs member" style="left:478px">
    <div class="portrait" role="img" aria-label="Black and white portrait of Pieter Vos"></div>
    <div class="plate"><b>Pieter Vos</b><small>Affiliate Partner<br>Transfer Pricing</small></div>
  </div>
  <div class="abs member" style="left:806px">
    <div class="portrait color" role="img" aria-label="Colour portrait of Owen Carter"></div>
    <div class="plate accent"><b>Owen Carter</b><div class="dots"><span></span><span></span><span></span></div></div>
  </div>
</section>

<section class="callback">
  <div class="abs callback-photo" role="img" aria-label="Businessman on the phone, tinted blue"></div>
  <h2 class="abs">REQUEST A CALL BACK</h2>
  <p class="abs">Would you like to speak to one of our experts? Just submit your contact details and we'll be in touch shortly. You can also email us if you prefer that type of communication.</p>
  <div class="abs field" style="left:133px">How we can help?</div>
  <div class="abs field" style="left:366px">Your Name *</div>
  <div class="abs field" style="left:598px">Your Phone Number *</div>
  <div class="abs submit">Submit <svg width="8" height="9" viewBox="0 0 8 9"><path d="M0 0l8 4.5L0 9z" fill="#fff"/></svg></div>
</section>

<section class="partners">
  <svg class="abs" style="left:88px;top:38px" width="14" height="26" viewBox="0 0 14 26"><path d="M12 1L2 13l10 12" fill="none" stroke="#333" stroke-width="1.6"/></svg>
  <div class="abs partner" style="left:142px;width:44px"></div>
  <div class="abs partner" style="left:220px;width:96px"></div>
  <div class="abs partner" style="left:356px;width:156px;height:16px;top:44px"></div>
  <div class="abs partner" style="left:552px;width:96px;height:22px;top:41px"></div>
  <div class="abs partner" style="left:688px;width:92px;height:18px;top:43px;background:#3277b5"></div>
  <div class="abs partner" style="left:816px;width:80px;background:#5a5f68"></div>
  <div class="abs partner" style="left:930px;width:120px;height:28px;top:38px"></div>
  <svg class="abs" style="left:1088px;top:38px" width="14" height="26" viewBox="0 0 14 26"><path d="M2 1l10 12L2 25" fill="none" stroke="#333" stroke-width="1.6"/></svg>
</section>

<footer class="footer">
  <div class="abs footer-frame"></div>
  <div class="abs brand-f"><span class="mark"></span><span class="name">KR APPRAISALS</span></div>
  <div class="abs city" style="left:192px;top:204px">Leiden</div>
  <div class="abs city" style="left:385px;top:204px">Amsterdam</div>
  <svg class="abs" style="left:192px;top:240px" width="12" height="16" viewBox="0 0 12 16"><path d="M6 15C2 10 1 8 1 6a5 5 0 0 1 10 0c0 2-1 4-5 9z" fill="none" stroke="#fff" stroke-width="1.2"/><circle cx="6" cy="6" r="1.8" fill="none" stroke="#fff"/></svg>
  <div class="abs addr" style="left:220px;top:240px">Parkweg 18<br>2311 AB Leiden<br>The Netherlands</div>
  <svg class="abs" style="left:385px;top:240px" width="12" height="16" viewBox="0 0 12 16"><path d="M6 15C2 10 1 8 1 6a5 5 0 0 1 10 0c0 2-1 4-5 9z" fill="none" stroke="#fff" stroke-width="1.2"/><circle cx="6" cy="6" r="1.8" fill="none" stroke="#fff"/></svg>
  <div class="abs addr" style="left:414px;top:240px">Keizerslaan 40<br>1071 KT Amsterdam<br>The Netherlands</div>
  <div class="abs tel" style="left:192px;top:309px"><svg width="16" height="12" viewBox="0 0 16 12"><path d="M1 4c0-2 3-3 7-3s7 1 7 3v1h-4V3H5v2H1z M3 6h10l1 5H2z" fill="none" stroke="#fff" stroke-width="1"/></svg>Tel: 070 555 0142</div>
  <div class="abs tel" style="left:385px;top:309px"><svg width="16" height="12" viewBox="0 0 16 12"><path d="M1 4c0-2 3-3 7-3s7 1 7 3v1h-4V3H5v2H1z M3 6h10l1 5H2z" fill="none" stroke="#fff" stroke-width="1"/></svg>Tel: 020 555 0187</div>
  <div class="abs map" role="img" aria-label="Street map of the region between Leiden and Amsterdam with office locations"></div>
  <div class="abs map-pin"></div>
  <div class="abs to-top"><svg width="12" height="8" viewBox="0 0 12 8"><path d="M1 7l5-5 5 5" fill="none" stroke="#fff" stroke-width="2"/></svg></div>
</footer>

<footer class="bottombar">
  <div class="abs copy">2019 - KR APPRAISALS  /  All Rights Reserved</div>
  <div class="abs links">Terms &amp; Conditions  /  Privacy Policy</div>
  <span class="abs social" style="left:995px"></span>
  <span class="abs social" style="left:1018px"></span>
  <span class="abs social" style="left:1044px"></span>
</footer>

</body>
</html>
```